Help design website for "Brightwater Civic Advisors" to advance the common good

Here is the Google doc link that lays out the design:

https://files.plumrivet.example/sheet/d/7QmTzR2wLx9KpVbN4hJcY8sEaUoFdG3iXkMnPq5rWt6/edit?usp=sharing

Here is the Google drive folder with the logos and photos: https://vault.plumrivet.example/open?id=4HkWp9LzQe2TxRvN8mBaYc3DsUoJfG6

The testimonials are being gathered and will be shared by Friday, 1/4.

The winner will also have to migrate the coding files to my hosting site.

Thank you for your help! Looking forward to seeing your designs.

Target Market(s)

Prospective clients

Industry/Entity Type

Non Profit

Coding

Coded - Design and coding required

Number of Pages Required

5+ page

Requirements
Must have
• Noted in the Google doc regarding layout.
Nice to have

```html
<!DOCTYPE html>
<html lang="en">
<head>
<meta charset="utf-8">
<title>Brightwater Civic Advisors — Services &amp; Testimonials</title>
<link href="https://fonts.googleapis.com/css2?family=Poppins:wght@500;600;700&family=Open+Sans:wght@400;600;700&display=swap" rel="stylesheet">
<style>
  :root{
    --brand-blue:#3b8fd8;
    --brand-blue-dark:#2f7fc6;
    --ink:#2b2b2b;
    --body-text:#3a3a3a;
    --footer-bg:#25262f;
    --pattern-bg:#eef0f3;
    --white:#ffffff;
  }
  *{box-sizing:border-box;margin:0;padding:0}
  html,body{width:760px;height:1200px;overflow:hidden;background:var(--white)}
  body{position:relative;font-family:"Open Sans",sans-serif;color:var(--body-text)}

  .site-header{position:absolute;left:0;top:0;width:760px;height:78px;background:var(--brand-blue)}
  .brand{position:absolute;left:90px;top:12px;display:flex;align-items:center;gap:10px}
  .brand-mark{width:38px;height:38px;background:var(--white)}
  .brand-name{font-family:"Poppins",sans-serif;font-weight:500;color:var(--white);
    font-size:12.5px;letter-spacing:3.2px;line-height:15px;text-transform:uppercase}
  .cta-button{position:absolute;left:466px;top:14px;width:203px;height:25px;border:2px solid var(--white);
    font-family:"Poppins",sans-serif;font-weight:700;font-size:8.4px;color:var(--white);
    display:flex;align-items:center;justify-content:center;text-transform:uppercase}
  .main-nav{position:absolute;top:56px;left:0;width:760px;height:14px}
  .main-nav a{position:absolute;font-family:"Poppins",sans-serif;font-weight:700;font-size:8.6px;
    color:var(--white);text-decoration:none;text-transform:uppercase}
  .main-nav a.is-active{border-bottom:1px solid var(--white);padding-bottom:1px}

  .hero{position:absolute;left:0;top:78px;width:760px;height:350px;
    background:linear-gradient(180deg,#cfc8bd 0%,#9a8a7a 45%,#4a4038 100%)}
  .hero-edge{position:absolute;left:0;top:340px;width:760px;height:90px}

  .intro{position:absolute;left:0;top:414px;width:760px;text-align:center}
  .intro h1{font-family:"Poppins",sans-serif;font-weight:600;font-size:16px;color:var(--ink)}
  .intro p{width:410px;margin:13px auto 0;font-size:9.6px;line-height:13px;color:var(--body-text)}

  .card{position:absolute;top:530px;width:278px;height:417px;background:var(--white);
    box-shadow:0 1px 6px rgba(0,0,0,.12)}
  .card--left{left:90px}
  .card--right{left:391px}
  .card-photo{position:relative;height:226px}
  .card--left .card-photo{background:linear-gradient(180deg,#e7b73c 0%,#b88a3a 55%,#2a2522 100%)}
  .card--right .card-photo{background:linear-gradient(180deg,#bdbdbd 0%,#6c6866 55%,#1f1e1f 100%)}
  .card-caption{position:absolute;left:0;bottom:0;width:100%;padding:0 18px 12px;
    background:linear-gradient(180deg,rgba(0,0,0,0),rgba(0,0,0,.75));padding-top:30px;
    font-family:"Poppins",sans-serif;font-weight:700;font-size:9.4px;line-height:11.5px;
    color:var(--white);text-transform:uppercase}
  .testimonial{position:relative;padding:20px 18px 0 32px}
  .testimonial .quote-open,.testimonial .quote-close{font-family:"Poppins",sans-serif;font-weight:700;
    font-size:22px;line-height:1;color:var(--ink);position:absolute}
  .testimonial .quote-open{left:18px;top:16px}
  .testimonial blockquote{font-size:8.7px;line-height:11.2px;color:var(--body-text)}
  .testimonial .quote-close{position:relative;display:inline-block;height:10px;top:4px;margin-left:4px}
  .testimonial cite{display:block;font-style:normal;font-size:8.7px;line-height:11.2px;margin-top:16px;color:var(--body-text)}
  .testimonial cite strong{font-weight:700}

  .pattern-band{position:absolute;left:0;top:952px;width:760px;height:120px;background:var(--pattern-bg)}
  .site-footer{position:absolute;left:0;top:990px;width:760px;height:210px}
  .footer-brand{position:absolute;left:90px;top:1092px;display:flex;align-items:center;gap:12px}
  .footer-brand .brand-mark{width:44px;height:44px;background:var(--brand-blue)}
  .footer-brand .brand-name{font-size:15px;letter-spacing:4px;line-height:19px}
  .footer-divider{position:absolute;left:388px;top:1076px;width:1px;height:90px;background:#44454f}
  .footer-menu{position:absolute;left:426px;top:1088px;color:var(--white)}
  .footer-menu h2{font-family:"Open Sans",sans-serif;font-weight:700;font-size:7.4px;letter-spacing:.3px}
  .footer-menu ul{list-style:none;display:flex;margin-top:12px;font-size:7.2px}
  .footer-menu li+li::before{content:"|";margin:0 7px}
  .copyright{position:absolute;left:426px;top:1148px;font-size:6.8px;color:var(--white)}
</style>
</head>
<body>
  <header class="site-header">
    <div class="brand">
      <span class="brand-mark"></span>
      <span class="brand-name">Brightwater<br>Civic<br>Advisors</span>
    </div>
    <a class="cta-button">Book a complimentary consultation</a>
    <nav class="main-nav">
      <a style="left:356px">About</a>
      <a class="is-active" style="left:406px">Services &amp; Testimonials</a>
      <a style="left:534px">Media &amp; Impact</a>
      <a style="left:626px">Contact</a>
    </nav>
  </header>

  <div class="hero" role="img" aria-label="Nora speaking to a seated group of students inside an art gallery"></div>
  <svg class="hero-edge" width="760" height="90" viewBox="0 0 760 90">
    <polygon points="0,81 381,19 760,81 760,90 0,90" fill="#3b8fd8"/>
    <polygon points="0,88 381,25 760,88 760,90 0,90" fill="#ffffff"/>
  </svg>

  <section class="intro">
    <h1>Group Facilitation &amp; Leadership Training</h1>
    <p>Nora has facilitated student groups, experiential learning activities, and dialogues on social justice issues, such as power and privilege, education, and poverty. She has developed curriculum and lesson plans for students to gain essential civic leadership competencies.</p>
  </section>

  <article class="card card--left">
    <div class="card-photo" role="img" aria-label="Group of participants posing in front of a yellow wall at a community theater">
      <div class="card-caption">Nora organizing an outing to a community theater to learn about immigrant stories</div>
    </div>
    <div class="testimonial">
      <span class="quote-open">&ldquo;</span>
      <blockquote>Nora is one of the most talented and effective group facilitators I have ever worked with. It's obvious that she has years of experience designing and delivering dynamic, transformative trainings for groups from many different backgrounds, ages, and industries. She has the unique ability to not only provide new insight for her clients, but to engage and inspire her groups to continue their learning and growth long after her trainings. Nora is also an absolute blast to work with!<span class="quote-close">&rdquo;</span></blockquote>
      <cite><strong>Theo Marsh,</strong> Chief Operations &amp; Growth Officer, Open Horizons</cite>
    </div>
  </article>

  <article class="card card--right">
    <div class="card-photo" role="img" aria-label="Nora leading a discussion with high school students around a table">
      <div class="card-caption">Nora facilitating a college access workshop for high school students</div>
    </div>
    <div class="testimonial">
      <span class="quote-open">&ldquo;</span>
      <blockquote>In my 10 years in the education field across two different continents, I have never worked with such an incredible leader. Nora's calm but relentless disposition pushed our students to truly reflect and lead to unprecedented growth. Even as a fellow educator, I learned so much from Nora about myself and my craft. Her work is truly inspirational and life-changing.<span class="quote-close">&rdquo;</span></blockquote>
      <cite style="margin-top:30px"><strong>Dana Whitfield</strong> Dean of Culture, Lakeview College Prep, Northgate Network of Charter Schools</cite>
    </div>
  </article>

  <div class="pattern-band" role="img" aria-label="Faint light grey decorative band"></div>
  <svg class="site-footer" width="760" height="210" viewBox="0 0 760 210">
    <polygon points="0,74 381,6 760,74 760,210 0,210" fill="#25262f"/>
  </svg>
  <div class="footer-brand">
    <span class="brand-mark"></span>
    <span class="brand-name">Brightwater<br>Civic<br>Advisors</span>
  </div>
  <div class="footer-divider"></div>
  <nav class="footer-menu">
    <h2>MENU</h2>
    <ul>
      <li>ABOUT</li>
      <li>SERVICES &amp; TESTIMONIALS</li>
      <li>MEDIA &amp; IMPACT</li>
      <li>CONTACT</li>
    </ul>
  </nav>
  <p class="copyright">Copyrights @ 2019 All Rights Reserved</p>
</body>
</html>
```